Realtor branding business card

modern, simple and self branding. Broker office logo needs to be used but not emphasized. Looking to brand myself

Target Market(s)

buyers, sellers and investors

Industry/Entity Type

Realtor

Contact Information for Business Card

Sample of my current business card on file

Requirements
Must have
• my website - tobiasmerrowkl.com
• Realtor logo
• Fair housing logo
Nice to have
• Colors from office logo but not a must
Should not have
• Do not want headshot

```html
<!DOCTYPE html>
<html lang="en">
<head>
<meta charset="utf-8">
<title>Tobias Merrow – Business Card</title>
<link href="https://fonts.googleapis.com/css2?family=Open+Sans:wght@400;600;800&display=swap" rel="stylesheet">
<style>
  :root{
    --stage:#e9e9ea;
    --brand-red:#ee2e24;
    --brand-navy:#2a1a7a;
    --ink:#3a3a3a;
    --paper:#ffffff;
  }
  *{margin:0;padding:0;box-sizing:border-box}
  html,body{width:1200px;height:782px;overflow:hidden;background:var(--stage);font-family:"Open Sans",Arial,sans-serif}
  .stage{position:relative;width:1200px;height:782px}
  .card{position:absolute;top:236px;width:540px;height:309px;overflow:hidden;box-shadow:0 8px 24px rgba(0,0,0,.18)}
  .card--front{left:40px;background:var(--brand-red);display:flex;flex-direction:column;align-items:center;justify-content:center;gap:28px}
  .card--back{left:620px;background:var(--paper)}
  .brand-name{font-weight:800;letter-spacing:-.5px;line-height:1.05;text-align:center}
  .card--front .brand-name{color:var(--paper);font-size:40px}
  .badges{display:flex;gap:26px}
  .badge{width:34px;height:34px;border:3px solid var(--paper);border-radius:3px}
  .agent{position:absolute;left:28px;top:26px}
  .agent__name{color:var(--brand-navy);font-size:19px;font-weight:600;letter-spacing:.3px}
  .agent__title{color:var(--brand-red);font-size:13px;margin-top:-2px}
  .contacts{position:absolute;left:28px;top:140px;list-style:none;color:var(--ink);font-size:14px;line-height:21px}
  .contacts li{display:flex;align-items:center;gap:6px}
  .contacts svg{width:11px;height:11px;fill:var(--brand-navy)}
  .card--back .brand-name{position:absolute;right:40px;top:122px;color:var(--brand-navy);font-size:30px;width:250px}
  .address{position:absolute;right:40px;top:212px;text-align:right;color:var(--ink);font-size:14px;line-height:19px}
  .stripes{position:absolute;left:0;bottom:0;width:540px;height:40px}
</style>
</head>
<body>
<main class="stage">
  <section class="card card--front" aria-label="Card front">
    <p class="brand-name">Brightgate<br>Realty Group</p>
    <div class="badges">
      <span class="badge" aria-label="Fair housing badge"></span>
      <span class="badge" aria-label="Realtor badge"></span>
    </div>
  </section>

  <section class="card card--back" aria-label="Card back">
    <div class="agent">
      <p class="agent__name">TOBIAS MERROW, PA</p>
      <p class="agent__title">Realtor</p>
    </div>
    <ul class="contacts">
      <li><svg viewBox="0 0 12 12"><path d="M2 1h3l1 3-2 1a7 7 0 0 0 3 3l1-2 3 1v3c0 1-1 1-1 1C5 11 1 7 1 2c0 0 0-1 1-1z"/></svg>555.394.0167</li>
      <li><svg viewBox="0 0 12 12"><path d="M3 0h6a1 1 0 0 1 1 1v10a1 1 0 0 1-1 1H3a1 1 0 0 1-1-1V1a1 1 0 0 1 1-1zm0 2v7h6V2z"/></svg>555.712.0480</li>
      <li><svg viewBox="0 0 12 12"><circle cx="6" cy="6" r="5.5"/></svg>tobiasmerrowkl.com</li>
    </ul>
    <p class="brand-name">Brightgate<br>Realty Group</p>
    <p class="address">418 Linden Harbor<br>Dr. Maple Springs<br>FL 30519</p>
    <svg class="stripes" viewBox="0 0 540 40" preserveAspectRatio="none" aria-hidden="true">
      <polygon points="0,8 250,30 250,40 0,40" fill="var(--brand-navy)"/>
      <polygon points="262,16 540,20 540,40 244,40" fill="var(--brand-red)"/>
    </svg>
  </section>
</main>
</body>
</html>
```